Corporate Template

Looking for a set of corporate slides to be made which contain multiple different slides and orientations. Looking for at least 8 to 10 different master pages plus a Coversheet and closeout page. Incorporating a color palate similar to our logo coloring is preferred.
I have attached a logo.
I like the amber quill works designs best so far. They seem to fit what I'm looking for in terms of visual appearance.
Reason: I'm trying to allow time for a couple new designers to incorporate some changes I requested to their existing designs.

```html
<!DOCTYPE html>
<html lang="en">
<head>
<meta charset="utf-8">
<title>Corporate Slide – Bullet List</title>
<link href="https://fonts.googleapis.com/css2?family=Ubuntu:wght@400;500;700&display=swap" rel="stylesheet">
<style>
  :root {
    --brand-deep: #2a66a6;
    --brand-mid: #3b7dbe;
    --brand-light: #76bbf2;
    --title-blue: #93cbff;
    --copyright-blue: #86c3ff;
    --text-dark: #3a3a3a;
    --white: #ffffff;
    --page-bg: #ffffff;
  }
  * { box-sizing: border-box; margin: 0; padding: 0; }
  html, body { width: 1200px; height: 900px; overflow: hidden; background: var(--page-bg); }
  .slide {
    position: relative;
    width: 1200px;
    height: 900px;
    overflow: hidden;
    font-family: "Ubuntu", "Segoe UI", sans-serif;
    background: var(--page-bg);
  }
  .header-band {
    position: absolute;
    left: 0; top: 0;
    width: 1200px; height: 93px;
    background: linear-gradient(90deg, var(--brand-mid) 0%, var(--brand-deep) 100%);
    border-bottom: 6px solid var(--brand-light);
  }
  .slide-title {
    position: absolute;
    left: 24px; top: 24px;
    font-size: 39px;
    font-weight: 500;
    color: var(--title-blue);
    letter-spacing: 0.2px;
  }
  .header-mark {
    position: absolute;
    right: 15px; top: 11px;
    width: 74px; height: 74px;
  }
  .bullet-list {
    position: absolute;
    left: 63px; top: 192px;
    list-style: none;
  }
  .bullet-item {
    display: flex;
    align-items: center;
    height: 93px;
    font-size: 22px;
    font-weight: 500;
    color: var(--text-dark);
  }
  .bullet-icon { width: 31px; height: 31px; margin-right: 21px; flex: none; }
  .footer-wave {
    position: absolute;
    left: 0; top: 0;
    width: 1200px; height: 900px;
  }
  .brand-name {
    position: absolute;
    left: 33px; top: 818px;
    font-size: 30px;
    font-weight: 500;
    color: var(--white);
  }
  .copyright {
    position: absolute;
    left: 786px; top: 864px;
    font-size: 21px;
    color: var(--copyright-blue);
  }
  .page-number {
    position: absolute;
    left: 1145px; top: 831px;
    width: 40px; height: 40px;
    border: 2px solid var(--white);
    border-radius: 50%;
    color: var(--white);
    font-size: 16px;
    font-weight: 700;
    display: flex; align-items: center; justify-content: center;
  }
</style>
</head>
<body>
<div class="slide">
  <header class="header-band">
    <h1 class="slide-title">Persentation Title here</h1>
    <svg class="header-mark" viewBox="0 0 74 74" aria-hidden="true">
      <circle cx="37" cy="37" r="34" fill="none" stroke="var(--white)" stroke-width="3"/>
    </svg>
  </header>

  <ul class="bullet-list">
    <li class="bullet-item"><svg class="bullet-icon" viewBox="0 0 31 31" aria-hidden="true"><circle cx="15.5" cy="15.5" r="15.5" fill="var(--brand-deep)"/><path d="M12 9 L19 15.5 L12 22" fill="none" stroke="var(--white)" stroke-width="3.5" stroke-linecap="round" stroke-linejoin="round"/></svg>Lorem ipsum dolor sit ipsum Lorem ipsum dolor sit ipsum Lorem ipsum dolor.</li>
    <li class="bullet-item"><svg class="bullet-icon" viewBox="0 0 31 31" aria-hidden="true"><circle cx="15.5" cy="15.5" r="15.5" fill="var(--brand-deep)"/><path d="M12 9 L19 15.5 L12 22" fill="none" stroke="var(--white)" stroke-width="3.5" stroke-linecap="round" stroke-linejoin="round"/></svg>Lorem ipsum dolor sit ipsum Lorem ipsum dolor sit ipsum Lorem ipsum dolor.</li>
    <li class="bullet-item"><svg class="bullet-icon" viewBox="0 0 31 31" aria-hidden="true"><circle cx="15.5" cy="15.5" r="15.5" fill="var(--brand-deep)"/><path d="M12 9 L19 15.5 L12 22" fill="none" stroke="var(--white)" stroke-width="3.5" stroke-linecap="round" stroke-linejoin="round"/></svg>Lorem ipsum dolor sit ipsum Lorem ipsum dolor sit ipsum Lorem ipsum dolor.</li>
    <li class="bullet-item"><svg class="bullet-icon" viewBox="0 0 31 31" aria-hidden="true"><circle cx="15.5" cy="15.5" r="15.5" fill="var(--brand-deep)"/><path d="M12 9 L19 15.5 L12 22" fill="none" stroke="var(--white)" stroke-width="3.5" stroke-linecap="round" stroke-linejoin="round"/></svg>Lorem ipsum dolor sit ipsum Lorem ipsum dolor sit ipsum Lorem ipsum dolor.</li>
    <li class="bullet-item"><svg class="bullet-icon" viewBox="0 0 31 31" aria-hidden="true"><circle cx="15.5" cy="15.5" r="15.5" fill="var(--brand-deep)"/><path d="M12 9 L19 15.5 L12 22" fill="none" stroke="var(--white)" stroke-width="3.5" stroke-linecap="round" stroke-linejoin="round"/></svg>Lorem ipsum dolor sit ipsum Lorem ipsum dolor sit ipsum Lorem ipsum dolor.</li>
  </ul>

  <svg class="footer-wave" viewBox="0 0 1200 900" aria-hidden="true">
    <defs>
      <linearGradient id="footerFill" x1="0" y1="0" x2="1" y2="0">
        <stop offset="0" stop-color="#2f6cad"/>
        <stop offset="1" stop-color="#3a7bbd"/>
      </linearGradient>
    </defs>
    <path d="M0,735 C300,800 520,848 700,842 C900,834 1050,760 1200,688 L1200,900 L0,900 Z" fill="url(#footerFill)"/>
    <path d="M0,735 C300,800 520,848 700,842 C900,834 1050,760 1200,688" fill="none" stroke="var(--brand-light)" stroke-width="4"/>
  </svg>

  <div class="brand-name">Meridian Neuro Labs</div>
  <p class="copyright">Copyright text here</p>
  <div class="page-number">01</div>
</div>
</body>
</html>
```